New tech executive consulting company needs professionally branded document templates

We are a new business selling fractional board advisory and go-to-market consulting services into the Technology space. Tessaly Brink are experts in providing high-quality executive-level leaders on a part-time basis to tech companies in need of their expertise. We work closely with clients to understand their business needs, challenges, and goals, and provides customised solutions to help them succeed. Due to our audience we need the design to have a high quality, executive look and feel.

Our first website is live and can be found at tessalybrink.example. We also already have a logo which I've uploaded. Our brand is clean and uses orange to give it colour and an identity that stands out.

We need some document master templates created so we can create our own presentations (Google Slides & Powerpoint), PDF documents, and Word templates, and ideally also a LinkedIn banner.

```html
<!DOCTYPE html>
<html lang="en">
<head>
<meta charset="utf-8">
<title>Tessaly Brink – Presentation Templates</title>
<link href="https://fonts.googleapis.com/css2?family=Montserrat:wght@300;400;500;600;700;800&display=swap" rel="stylesheet">
<style>
:root{
  --bg:#d3d4d6;
  --orange:#ec834b;
  --navy:#27303b;
  --navy-deep:#1b222b;
  --ink:#3a3f45;
  --muted:#6b7077;
  --rule:#d9dadc;
  --sage:#b9c9c9;
  --white:#ffffff;
}
*{box-sizing:border-box;margin:0;padding:0}
html,body{width:1200px;height:1069px;overflow:hidden;background:var(--bg);font-family:'Montserrat',sans-serif;color:var(--ink)}
.board{position:relative;width:1200px;height:1069px}
.slide{position:absolute;width:304px;height:190px;background:var(--white);overflow:hidden;box-shadow:0 10px 8px -6px rgba(0,0,0,.28)}
.slide.dark{background:var(--navy);color:var(--white)}
.photo{position:absolute;inset:0;background:radial-gradient(ellipse at 70% 40%,#4a5360 0%,#2c3440 45%,#1b222b 100%)}
.photo.tint::after{content:"";position:absolute;inset:0;background:rgba(30,38,48,.55)}
.photo.mono{background:linear-gradient(120deg,#e8e8e8 0%,#8a8d91 40%,#3b3e42 75%,#1c1d1f 100%)}
.heading{position:absolute;left:10px;top:8px;font-size:10px;font-weight:500;color:var(--orange)}
.dark .heading{color:var(--white)}
.brand{position:absolute;right:8px;top:9px;font-size:4.6px;font-weight:800;letter-spacing:.4px;color:var(--navy);display:flex;align-items:center;gap:2px}
.brand i{display:block;width:3px;height:3px;background:var(--orange)}
.dark .brand{color:var(--white)}
.footer{position:absolute;right:8px;bottom:7px;font-size:3.8px;color:var(--ink);display:flex;gap:3px;align-items:center}
.footer b{font-weight:400;border-left:.6px solid var(--orange);padding-left:2px;height:8px;line-height:8px}
.dark .footer{color:var(--white)}
.body{position:absolute;font-size:3.6px;line-height:8.6px;color:var(--ink);text-align:justify}
.body p+p{margin-top:5px}
.orange{color:var(--orange)}
/* cover */
.logo-tab{position:absolute;left:19px;top:0;width:77px;height:43px;background:var(--white);border-radius:0 0 5px 5px;display:flex;align-items:center;justify-content:center;gap:3px;font-size:7px;font-weight:800;color:var(--navy);letter-spacing:.4px}
.logo-tab i{width:5px;height:5px;background:var(--orange)}
.hero{position:absolute;left:20px;font-size:12.6px;line-height:16.4px;font-weight:400;color:var(--white)}
.hero .orange{color:var(--orange)}
.hero-rule{position:absolute;left:20px;width:52px;height:1px;background:var(--white)}
.hero-note{position:absolute;left:20px;top:129px;width:140px;font-size:3.4px;line-height:5.2px;color:#dfe2e6}
.pill{position:absolute;left:19px;top:147px;background:var(--orange);color:var(--white);font-size:4.2px;padding:1.5px 5px;border-radius:4px}
.url{position:absolute;left:20px;top:177px;font-size:4.2px;color:var(--white)}
/* cards */
.svc{position:absolute;height:27px;background:var(--navy);border-radius:4px 5px 5px 14px;color:var(--white)}
.svc .dot{position:absolute;left:-1px;top:-2px;width:31px;height:31px;border-radius:50%;background:var(--orange);border:2.5px solid var(--white);box-shadow:0 0 0 1px var(--navy)}
.svc h4{position:absolute;left:37px;top:3px;font-size:5px;font-weight:500;color:var(--orange)}
.svc p{position:absolute;left:37px;top:10px;right:4px;font-size:2.9px;line-height:3.6px;color:#d8dbe0}
.svc svg{position:absolute;left:7px;top:6px}
.side-title{position:absolute;left:185px;font-size:5px;font-weight:500;color:var(--orange)}
.side-text{position:absolute;left:185px;width:106px;font-size:3px;line-height:3.9px;color:var(--ink)}
.col-title{position:absolute;font-size:6.2px;font-weight:500;color:var(--orange)}
.bullets{position:absolute;list-style:none;font-size:3.7px;line-height:4.4px;text-align:justify;color:var(--ink)}
.bullets li{position:relative;padding-left:5px;margin-bottom:10px}
.bullets li::before{content:"";position:absolute;left:0;top:1.5px;width:1.6px;height:1.6px;background:var(--ink)}
.offer{position:absolute;top:49px;width:65px;height:102px;background:var(--orange);border-radius:12px 0 0 0;border-bottom:3.5px solid var(--navy);color:var(--white);text-align:center}
.offer .ico{width:12px;height:12px;border-radius:50%;background:var(--navy);margin:8px auto 0}
.offer h4{font-size:7.4px;font-weight:400;margin-top:8px}
.offer p{font-size:3.6px;line-height:4.4px;padding:3px 7px 0}
/* table */
.grid{position:absolute;left:16px;top:41px;width:272px;border-collapse:collapse;font-size:3.6px;color:var(--white)}
.grid th{background:var(--white);color:var(--navy);font-weight:400;height:13px;text-align:center;line-height:4.2px}
.grid th:first-child{text-align:left;padding-left:2px}
.grid td{height:12.3px;border-bottom:.6px solid rgba(255,255,255,.6);text-align:center}
.grid td:first-child{text-align:left;padding-left:2px}
.grid th.hl{background:var(--orange);color:var(--white)}
.grid .first{width:83px}
.hl-frame{position:absolute;left:99px;top:38px;width:47px;height:107px;border:1px solid var(--orange);border-radius:3px}
/* team */
.member{position:absolute;top:38px;width:52px;height:123px}
.member .panel{position:absolute;left:0;right:0;top:22px;bottom:0;background:var(--navy);border-radius:0 0 6px 6px}
.member .avatar{position:absolute;left:3px;top:0;width:46px;height:46px;border-radius:50%;background:var(--orange);border:3px solid var(--white)}
.member h4{position:absolute;top:56px;width:100%;text-align:center;font-size:7px;font-weight:400;color:var(--white)}
.member .bar{position:absolute;top:65px;left:17px;width:18px;height:1px;background:var(--orange)}
.member p{position:absolute;top:68px;left:4px;right:4px;font-size:2.9px;line-height:3.7px;text-align:justify;color:#d8dbe0}
/* infographic */
.info-title{position:absolute;top:34px;width:100%;text-align:center;font-size:12px;font-weight:600;letter-spacing:.4px;color:var(--orange)}
.info-note{position:absolute;top:51px;left:45px;right:45px;text-align:center;font-size:3px;line-height:4.8px;color:#e3e6ea}
.info-label{position:absolute;width:38px;font-size:2.6px;line-height:3.4px;color:#d9dce0}
.legend{position:absolute;left:228px;top:131px;font-size:4px;font-weight:600;color:var(--navy)}
.legend div{display:flex;align-items:center;gap:6px;height:8.3px}
.legend i{width:4px;height:4px;display:block}
</style>
</head>
<body>
<main class="board">

<!-- Row 1 -->
<section class="slide dark" style="left:95px;top:77px">
  <div class="photo tint" role="img" aria-label="Photo of executives meeting around a boardroom table"></div>
  <div class="logo-tab"><i></i>TESSALY BRINK</div>
  <h1 class="hero" style="top:76px">Experts in<br>providing <span class="orange">executive</span><br><span class="orange">leadership</span> on demand</h1>
  <div class="hero-rule" style="top:125px"></div>
  <p class="hero-note">Part-time executive leaders for technology companies ready to scale with confidence and a clear plan.</p>
  <span class="pill">15 July 2023</span>
  <span class="url">www.tessalybrink.example</span>
</section>

<section class="slide" style="left:447px;top:77px">
  <h2 class="heading">Heading Goes Here</h2>
  <div class="brand"><i></i>TESSALY BRINK</div>
  <div class="body" style="left:10px;top:32px;width:284px">
    <p>We place seasoned technology executives with growing companies on a flexible basis. Each leader brings board experience, clear judgement and a proven record in scaling teams, shaping strategy and building revenue. We listen first, then design support that fits your stage.</p>
    <p>We place seasoned technology executives with growing companies on a flexible basis. Each leader brings board experience, clear judgement and a proven record in scaling teams, shaping strategy and building revenue. We listen first, then design support that fits your stage.</p>
    <p>We place seasoned technology executives with growing companies on a flexible basis. Each leader brings board experience, clear judgement and a proven record in scaling teams, shaping strategy and building revenue. We listen first, then design support that fits your stage.</p>
  </div>
  <div class="footer">Tessaly Brink <b>01</b></div>
</section>

<section class="slide" style="left:800px;top:77px">
  <h2 class="heading">Project Team</h2>
  <div class="body" style="left:10px;top:32px;width:112px;text-align:left;font-size:3.5px">
    <p>A marketing strategy helps convey effective messages with the right twist of marketing approaches that will maximize your sales outcome and marketing activities.</p>
    <p>The objectives will be based on how you gain sales by acquiring and keeping customers.</p>
    <p>Marketing strategy's goal is to increase sales and achieve the advantage over other competitions. It includes short term and long term activities of marketing that has to do with the analysis of a company's situation and contribute to its objectives.</p>
  </div>
  <div class="photo mono" style="left:135px" role="img" aria-label="Black and white photo of business people among city skyscrapers"></div>
  <div class="brand" style="color:var(--white)"><i></i>TESSALY BRINK</div>
  <div class="footer" style="color:var(--white)">Tessaly Brink <b>01</b></div>
</section>

<!-- Row 2 -->
<section class="slide" style="left:95px;top:313px">
  <div class="brand"><i></i>TESSALY BRINK</div>
  <h2 class="heading" style="top:48px;line-height:11px;font-size:9.6px">CLIENT<br>DATA GRAPHS</h2>
  <div style="position:absolute;left:10px;top:81px;width:84px;height:.6px;background:var(--ink)"></div>
  <div class="body" style="left:10px;top:89px;width:108px;font-size:3.7px;line-height:7.3px">
    <p>Track results across each half year. Every ring shows one filter so leaders can compare progress at a glance and plan the next quarter.</p>
    <p>Keep the board informed with clear data.</p>
  </div>
  <svg style="position:absolute;left:134px;top:36px" width="122" height="122" viewBox="0 0 122 122">
    <g fill="none" transform="rotate(-90 61 61)">
      <circle cx="61" cy="61" r="56" stroke="var(--sage)" stroke-width="5" stroke-dasharray="264 88"/>
      <circle cx="61" cy="61" r="50" stroke="var(--orange)" stroke-width="5" stroke-dasharray="236 78" transform="rotate(4 61 61)"/>
      <circle cx="61" cy="61" r="44.5" stroke="var(--navy)" stroke-width="5" stroke-dasharray="208 72" transform="rotate(10 61 61)"/>
      <circle cx="61" cy="61" r="39.5" stroke="#111" stroke-width="3" stroke-dasharray="182 66" transform="rotate(16 61 61)"/>
    </g>
    <text x="61" y="61" text-anchor="middle" font-family="Montserrat,sans-serif" font-size="6.4" font-weight="700" fill="#111">January - June</text>
    <text x="61" y="70" text-anchor="middle" font-family="Montserrat,sans-serif" font-size="5.2" fill="#111">2020</text>
  </svg>
  <div class="legend">
    <div><i style="background:var(--sage)"></i>A Filltor</div>
    <div><i style="background:var(--orange)"></i>B Filltor</div>
    <div><i style="background:var(--navy)"></i>C Filltor</div>
    <div style="border-top:.6px solid var(--navy)"><i style="background:#111"></i>D Filltor</div>
  </div>
  <div class="footer">Tessaly Brink <b>01</b></div>
</section>

<section class="slide" style="left:447px;top:313px">
  <h2 class="heading" style="top:10px">Heading Goes Here</h2>
  <div class="brand"><i></i>TESSALY BRINK</div>
  <div class="body" style="left:10px;top:35px;width:284px">
    <p>We place seasoned technology executives with growing companies on a flexible basis. Each leader brings board experience, clear judgement and a proven record in scaling teams, shaping strategy and building revenue. We listen first, then design support that fits your stage.</p>
  </div>
  <div class="svc" style="left:12px;top:84px;width:135px"><span class="dot"></span><svg width="18" height="17" viewBox="0 0 18 17"><circle cx="8" cy="5" r="3.5" fill="#fff"/><path d="M1 16c0-5 3-7 7-7s7 2 7 7z" fill="#fff"/></svg><h4>Title Goes Here</h4><p>Short note on this service, its scope and the value it brings to your leadership team each week.</p></div>
  <div class="svc" style="left:158px;top:84px;width:138px"><span class="dot"></span><svg width="18" height="17" viewBox="0 0 18 17"><circle cx="8" cy="5" r="3.5" fill="#fff"/><path d="M1 16c0-5 3-7 7-7s7 2 7 7z" fill="#fff"/></svg><h4>Title Goes Here</h4><p>Short note on this service, its scope and the value it brings to your leadership team each week.</p></div>
  <div class="svc" style="left:12px;top:124px;width:135px"><span class="dot"></span><svg width="18" height="17" viewBox="0 0 18 17"><circle cx="8" cy="5" r="3.5" fill="#fff"/><path d="M1 16c0-5 3-7 7-7s7 2 7 7z" fill="#fff"/></svg><h4>Title Goes Here</h4><p>Short note on this service, its scope and the value it brings to your leadership team each week.</p></div>
  <div class="svc" style="left:158px;top:124px;width:138px"><span class="dot"></span><svg width="18" height="17" viewBox="0 0 18 17"><circle cx="8" cy="5" r="3.5" fill="#fff"/><path d="M1 16c0-5 3-7 7-7s7 2 7 7z" fill="#fff"/></svg><h4>Title Goes Here</h4><p>Short note on this service, its scope and the value it brings to your leadership team each week.</p></div>
  <div class="footer">Tessaly Brink <b>01</b></div>
</section>

<section class="slide" style="left:800px;top:313px">
  <h2 class="heading">Heading Goes Here</h2>
  <div class="brand"><i></i>TESSALY BRINK</div>
  <svg style="position:absolute;left:12px;top:62px" width="156" height="78" viewBox="0 0 156 78">
    <g stroke="#e3e4e6" stroke-width=".4">
      <line x1="4" y1="6" x2="152" y2="6"/><line x1="4" y1="14" x2="152" y2="14"/><line x1="4" y1="22" x2="152" y2="22"/><line x1="4" y1="30" x2="152" y2="30"/><line x1="4" y1="38" x2="152" y2="38"/><line x1="4" y1="46" x2="152" y2="46"/><line x1="4" y1="54" x2="152" y2="54"/><line x1="4" y1="62" x2="152" y2="62"/>
      <line x1="28" y1="6" x2="28" y2="70"/><line x1="52" y1="6" x2="52" y2="70"/><line x1="76" y1="6" x2="76" y2="70"/><line x1="100" y1="6" x2="100" y2="70"/><line x1="124" y1="6" x2="124" y2="70"/><line x1="148" y1="6" x2="148" y2="70"/>
    </g>
    <line x1="4" y1="2" x2="4" y2="70" stroke="#bbb" stroke-width=".5"/>
    <line x1="4" y1="70" x2="154" y2="70" stroke="#bbb" stroke-width=".5"/>
    <polyline points="16,69 26,41 34,60 52,52 76,69 90,58 100,69" fill="none" stroke="#111" stroke-width=".6"/>
    <polyline points="28,69 32,28 50,20 76,54 100,30 112,44 124,36 136,69" fill="none" stroke="var(--orange)" stroke-width=".6"/>
    <g fill="#111"><circle cx="16" cy="69" r=".9"/><circle cx="26" cy="41" r=".9"/><circle cx="34" cy="60" r=".9"/><circle cx="52" cy="52" r=".9"/><circle cx="76" cy="69" r=".9"/><circle cx="90" cy="58" r=".9"/></g>
    <g fill="var(--orange)"><circle cx="32" cy="28" r=".9"/><circle cx="50" cy="20" r=".9"/><circle cx="100" cy="30" r=".9"/><circle cx="112" cy="44" r=".9"/><circle cx="124" cy="36" r=".9"/></g>
  </svg>
  <h3 class="side-title" style="top:55px">Title Goes Here</h3>
  <p class="side-text" style="top:62px">Short note on this service, its scope and the value it brings to your leadership team each week.</p>
  <h3 class="side-title" style="top:88px">Title Goes Here</h3>
  <p class="side-text" style="top:95px">Short note on this service, its scope and the value it brings to your leadership team each week.</p>
  <h3 class="side-title" style="top:120px">Title Goes Here</h3>
  <p class="side-text" style="top:127px">Short note on this service, its scope and the value it brings to your leadership team each week.</p>
  <div class="footer">Tessaly Brink <b>01</b></div>
</section>

<!-- Row 3 -->
<section class="slide" style="left:95px;top:550px">
  <h2 class="heading" style="left:11px">Heading Goes Here</h2>
  <div class="brand"><i></i>TESSALY BRINK</div>
  <h3 class="col-title" style="left:16px;top:42px">Curabitur Dapibus Dignissim Dui.</h3>
  <ul class="bullets" style="left:16px;top:56px;width:130px">
    <li>Advisors join your leadership team part time, guide key decisions and help you hire, plan and sell with focus.</li>
    <li>Advisors join your leadership team part time, guide key decisions and help you hire, plan and sell with focus.</li>
    <li>Advisors join your leadership team part time, guide key decisions and help you hire, plan and sell with focus.</li>
  </ul>
  <h3 class="col-title" style="left:157px;top:42px">Curabitur Dapibus Dignissim Dui.</h3>
  <ul class="bullets" style="left:157px;top:56px;width:130px">
    <li>Advisors join your leadership team part time, guide key decisions and help you hire, plan and sell with focus.</li>
    <li>Advisors join your leadership team part time, guide key decisions and help you hire, plan and sell with focus.</li>
    <li>Advisors join your leadership team part time, guide key decisions and help you hire, plan and sell with focus.</li>
  </ul>
  <div class="footer">Tessaly Brink <b>01</b></div>
</section>

<section class="slide" style="left:447px;top:550px">
  <h2 class="heading" style="left:11px">Heading Goes Here</h2>
  <div class="brand"><i></i>TESSALY BRINK</div>
  <div class="offer" style="left:16px"><div class="ico"></div><h4>Heading</h4><p>Brief text for this card that explains one core offer in a few plain words for clients.</p></div>
  <div class="offer" style="left:88px"><div class="ico"></div><h4>Heading</h4><p>Brief text for this card that explains one core offer in a few plain words for clients.</p></div>
  <h3 class="col-title" style="left:163px;top:51px">Curabitur Dapibus Dignissim Dui.</h3>
  <ul class="bullets" style="left:164px;top:64px;width:123px">
    <li>Advisors join your leadership team part time, guide key decisions and help you hire, plan and sell with focus.</li>
    <li>Advisors join your leadership team part time, guide key decisions and help you hire, plan and sell with focus.</li>
    <li>Advisors join your leadership team part time, guide key decisions and help you hire, plan and sell with focus.</li>
  </ul>
  <div class="footer">Tessaly Brink <b>01</b></div>
</section>

<section class="slide dark" style="left:800px;top:550px">
  <div class="photo tint" role="img" aria-label="Dim photo of a team meeting in an office"></div>
  <h2 class="heading">Heading Goes Here</h2>
  <div class="brand"><i></i>TESSALY BRINK</div>
  <h3 class="info-title">INFOGRAPHIC CHART</h3>
  <p class="info-note">A simple view of how our advisors split their time across six areas of client work each month.</p>
  <svg style="position:absolute;left:107px;top:65px" width="94" height="94" viewBox="0 0 94 94">
    <circle cx="47" cy="47" r="41" fill="none" stroke="rgba(30,38,48,.85)" stroke-width="12"/>
    <circle cx="47" cy="47" r="26" fill="var(--orange)"/>
    <g fill="#fff"><circle cx="47" cy="41" r="4"/><path d="M39 55c0-6 4-8 8-8s8 2 8 8z"/><circle cx="38" cy="43" r="3"/><path d="M32 54c0-4 3-6 6-6 2 0 3 .5 3 .5-2 1.5-3 3.5-3 5.5z"/><circle cx="56" cy="43" r="3"/><path d="M62 54c0-4-3-6-6-6-2 0-3 .5-3 .5 2 1.5 3 3.5 3 5.5z"/></g>
    <g font-family="Montserrat,sans-serif" font-size="3.6" font-weight="600" fill="#fff" text-anchor="middle">
      <text x="47" y="4">50%</text><text x="47" y="93">50%</text>
      <text x="14" y="20" transform="rotate(-45 14 20)">50%</text><text x="80" y="20" transform="rotate(45 80 20)">50%</text>
      <text x="6" y="48" transform="rotate(-90 6 48)">50%</text><text x="89" y="48" transform="rotate(90 89 48)">50%</text>
      <text x="14" y="78" transform="rotate(45 14 78)">50%</text><text x="80" y="78" transform="rotate(-45 80 78)">50%</text>
    </g>
  </svg>
  <g></g>
  <svg style="position:absolute;left:46px;top:83px" width="10" height="72" viewBox="0 0 10 72">
    <g fill="var(--orange)"><circle cx="5" cy="4" r="3"/><rect x="1" y="27" width="8" height="6" rx="1" fill="none" stroke="#fff" stroke-width=".8"/><rect x="3" y="55" width="4" height="7"/></g>
  </svg>
  <p class="info-label" style="left:64px;top:84px">Short label for this area.</p>
  <p class="info-label" style="left:64px;top:110px">Short label for this area.</p>
  <p class="info-label" style="left:64px;top:137px">Short label for this area.</p>
  <svg style="position:absolute;left:249px;top:82px" width="10" height="72" viewBox="0 0 10 72">
    <g fill="var(--orange)"><path d="M5 0a4 4 0 0 1 2 7.5V10H3V7.5A4 4 0 0 1 5 0z"/><circle cx="5" cy="30" r="4"/><circle cx="5" cy="57" r="4" fill="none" stroke="var(--orange)" stroke-width="1.6"/></g>
  </svg>
  <p class="info-label" style="left:221px;top:84px;left:222px">Short label for this area.</p>
  <p class="info-label" style="left:222px;top:110px">Short label for this area.</p>
  <p class="info-label" style="left:222px;top:137px">Short label for this area.</p>
  <div class="footer">Tessaly Brink <b>01</b></div>
</section>

<!-- Row 4 -->
<section class="slide dark" style="left:95px;top:787px">
  <div class="photo tint" role="img" aria-label="Dim photo of colleagues talking in an office"></div>
  <h2 class="heading" style="left:11px">Heading Goes Here</h2>
  <div class="brand"><i></i>TESSALY BRINK</div>
  <table class="grid">
    <tr><th class="first">Heading Goes Here</th><th class="hl">Heading<br>Goes Here</th><th>Heading<br>Goes Here</th><th>Heading<br>Goes Here</th><th>Heading<br>Goes Here</th></tr>
    <tr><td>Lorem Ipsum Goes Here</td><td>23</td><td>12</td><td>78</td><td>12</td></tr>
    <tr><td>Lorem Ipsum Goes Here</td><td>45</td><td>56</td><td>12</td><td>56</td></tr>
    <tr><td>Lorem Ipsum Goes Here</td><td>78</td><td>76</td><td>34</td><td>76</td></tr>
    <tr><td>Lorem Ipsum Goes Here</td><td>22</td><td>12</td><td>55</td><td>12</td></tr>
    <tr><td>Lorem Ipsum Goes Here</td><td>34</td><td>66</td><td>45</td><td>66</td></tr>
    <tr><td>Lorem Ipsum Goes Here</td><td>67</td><td>47</td><td>78</td><td>47</td></tr>
    <tr><td>Lorem Ipsum Goes Here</td><td>87</td><td>67</td><td>12</td><td>67</td></tr>
  </table>
  <div class="hl-frame"></div>
  <div class="footer">Tessaly Brink <b>01</b></div>
</section>

<section class="slide" style="left:447px;top:787px">
  <h2 class="heading" style="left:11px">Heading Goes Here</h2>
  <div class="brand"><i></i>TESSALY BRINK</div>
  <div class="member" style="left:24px"><div class="panel"></div><div class="avatar"></div><h4>Name Here</h4><span class="bar"></span><p>Senior executive with many years leading growth at software firms, now advising boards on strategy, sales and scaling teams.</p></div>
  <div class="member" style="left:91px"><div class="panel"></div><div class="avatar"></div><h4>Name Here</h4><span class="bar"></span><p>Senior executive with many years leading growth at software firms, now advising boards on strategy, sales and scaling teams.</p></div>
  <div class="member" style="left:158px"><div class="panel"></div><div class="avatar"></div><h4>Name Here</h4><span class="bar"></span><p>Senior executive with many years leading growth at software firms, now advising boards on strategy, sales and scaling teams.</p></div>
  <div class="member" style="left:226px"><div class="panel"></div><div class="avatar"></div><h4>Name Here</h4><span class="bar"></span><p>Senior executive with many years leading growth at software firms, now advising boards on strategy, sales and scaling teams.</p></div>
  <svg style="position:absolute;left:0;top:0;pointer-events:none" width="304" height="190" viewBox="0 0 304 190">
    <g fill="#fff">
      <circle cx="50" cy="59" r="4"/><path d="M43 68c0-4 3-6 7-6s7 2 7 6z"/>
      <circle cx="117" cy="59" r="4"/><path d="M110 68c0-4 3-6 7-6s7 2 7 6z"/>
      <circle cx="184" cy="59" r="4"/><path d="M177 68c0-4 3-6 7-6s7 2 7 6z"/>
      <circle cx="252" cy="59" r="4"/><path d="M245 68c0-4 3-6 7-6s7 2 7 6z"/>
    </g>
  </svg>
  <div class="footer">Tessaly Brink <b>01</b></div>
</section>

<section class="slide dark" style="left:800px;top:787px">
  <div class="photo tint" role="img" aria-label="Photo of executives meeting around a boardroom table"></div>
  <div class="logo-tab" style="left:20px;width:72px;height:42px"><i></i>TESSALY BRINK</div>
  <h2 class="hero" style="top:80px">Experts in<br>providing <span class="orange">executive</span><br><span class="orange">leadership</span> on demand</h2>
  <div class="hero-rule" style="top:128px;width:66px"></div>
  <p style="position:absolute;left:16px;top:146px;font-size:23px;font-weight:700;letter-spacing:.5px;color:var(--white)">THANK YOU!</p>
  <div style="position:absolute;left:16px;top:187px;width:68px;height:1px;background:var(--white)"></div>
</section>

</main>
</body>
</html>
```